Professional Engineering Web Design

Project Brief: Website Redesign for Mechanical Design Consultancy
Project Overview
I want to update and improve my current website to create a more professional, modern, and high-credibility online presence for my mechanical design consultancy.

Current site: https://valtorix.design/

The new website must communicate expertise, precision, and trust—matching the standard of top engineering and product design agencies.

Reference Websites (Style + Structure Inspiration)
These represent the quality, cleanliness, and professionalism I want to achieve:

https://plinthwaredesign.com/
https://www.sorvane.com/
https://bramlow-uk.com/
Brand Look
Professional, modern, engineering-focused aesthetic
Clean layouts and strong typography
High-quality imagery conveying precision, innovation, and mechanical expertise
Colour scheme and styling must follow my existing logo (attached in project)
Platform Requirements
The website must be built on WordPress
Should use a clean, flexible theme or modern page builder (Elementor, Gutenberg, Bricks, or similar)
Avoid overly complex custom coding so I can easily edit content later
Final deliverable must allow me to manage and update content without developer assistance
Functionality
Fast-loading, lightweight, and smooth user experience
Clean animations and transitions similar to the reference sites
Fully mobile responsive
Clear navigation and strong visual hierarchy
Contact forms optimised for lead generation
Optional: subtle scroll effects, case study sliders, icon animations, etc.
SEO Aspirations
Developer should recommend and implement a modern SEO strategy
Proper on-page SEO setup (titles, meta, schema, alt tags, heading structure)
Optimised site architecture for ranking and crawling
Aim: Generate leads through improved visibility and keyword targeting
Optional but useful: Google Analytics, Google Search Console setup
User Journeys
(Recommended structure)

The site should be crafted around clear, intuitive journeys for each type of visitor:

Potential new clients
Quickly understand what services I offer
View examples of past work / case studies
See credibility indicators (process, expertise, industries served)
Easily contact me or request a project discussion
Returning clients
Access updated portfolio items
Find contact details or book follow-up work easily
General visitors discovering through SEO
Be guided to valtorix service areas
Understand my value proposition quickly
Be invited to learn more or make contact
The developer should design the structure to support these journeys smoothly.

Maintenance Expectations
Website will be maintained by me, so it should be easy to update using relatively basic WordPress skills
Use modular templates and simple backend structure
Avoid unnecessary plugins
Provide brief handover documentation if required
Hosting Preferences
Site is currently hosted via a family member
Open to discussing moving to a paid, reliable hosting provider if preferable for performance and maintainability
Developer may advise on the best hosting setup for WordPress
Content
Most content can be taken from the existing website
Developer is welcome to suggest improvements to structure, layout, and imagery
Must remain easy for me to edit or add new content later (e.g., new projects)
Deliverables
Fully built WordPress website
Clean, professional, modern design inspired by the reference sites
Mobile-responsive across all devices
SEO-ready structure and optimisations
Transfer of website and admin rights
Any design assets, templates, or documentation used

```html
<!DOCTYPE html>
<html lang="en">
<head>
<meta charset="utf-8">
<title>Valtorix Design – Precision Engineering &amp; Mechanical Design</title>
<link href="https://fonts.googleapis.com/css2?family=Outfit:wght@300;400;500;600;700;800&family=Bree+Serif&display=swap" rel="stylesheet">
<style>
:root{
  --blue:#2f5de6;
  --blue-dark:#2149c9;
  --blue-soft:#dfe6fb;
  --ink:#141414;
  --text:#2b2b2b;
  --muted:#555;
  --grey-bg:#f1f1f1;
  --white:#fff;
  --line:#c9cfdc;
}
*{margin:0;padding:0;box-sizing:border-box}
html,body{width:1200px;height:4515px;overflow:hidden}
body{font-family:"Outfit",sans-serif;color:var(--text);background:var(--white);position:relative}
section,header,footer{position:absolute;left:0;width:1200px}
.abs{position:absolute}
.eyebrow{color:var(--blue);font-size:17px;font-weight:400;letter-spacing:.5px}
.section-title{color:var(--ink);font-size:31px;font-weight:700;letter-spacing:.2px}
.center{left:0;width:1200px;text-align:center}
.body-copy{font-size:13.5px;line-height:24px;color:var(--text)}
.btn{display:flex;align-items:center;justify-content:center;background:var(--blue);color:var(--white);font-size:12px;font-weight:500;border-radius:22px;letter-spacing:.3px}

/* header */
.topbar{top:0;left:508px;width:692px;height:38px;background:var(--blue);border-bottom-left-radius:4px}
.topbar .social{position:absolute;top:7px;width:25px;height:25px;border:1.5px solid var(--white);border-radius:50%}
.topbar .contact{position:absolute;top:10px;color:var(--white);font-size:12px;display:flex;align-items:center;gap:8px}
.site-header{top:0;height:100px;z-index:2}
.brand{position:absolute;left:140px;top:9px;width:132px;height:122px;background:var(--white);border-radius:0 0 10px 10px;box-shadow:0 3px 10px rgba(0,0,0,.15);display:flex;flex-direction:column;align-items:center;justify-content:center;gap:8px}
.brand .mark{width:46px;height:46px;border-radius:50%;background:var(--blue)}
.brand .name{font-size:26px;font-weight:500;color:var(--blue);letter-spacing:1px}
.nav{position:absolute;top:60px;left:0;width:1200px}
.nav a{position:absolute;font-size:12px;color:#333;text-decoration:none;letter-spacing:.3px}
.nav a.active{color:var(--blue)}

/* hero */
.hero{top:100px;height:575px}
.hero-photo{position:absolute;left:0;top:0;width:1200px;height:562px;background:linear-gradient(110deg,#c9d1dc 0%,#8d98a8 35%,#3d4656 60%,#20262f 100%)}
.hero-stripe{position:absolute;left:0;top:562px;width:1200px;height:13px;background:var(--blue);border-top:4px solid var(--white)}
.hero-circle{position:absolute;left:140px;top:40px;width:438px;height:438px;border-radius:50%;background:var(--blue);box-shadow:0 0 0 6px rgba(47,93,230,.35)}
.hero-title{position:absolute;left:140px;top:125px;width:438px;text-align:center;font-family:"Bree Serif",serif;color:var(--white);font-size:38px;line-height:42px}
.hero-sub{position:absolute;left:200px;top:303px;width:318px;text-align:center;color:var(--white);font-size:14.5px;line-height:23px}
.hero-btn{position:absolute;left:291px;top:387px;width:136px;height:39px;background:var(--white);color:#222;border-radius:22px;font-size:12px;display:flex;align-items:center;justify-content:center;box-shadow:0 0 0 3px rgba(255,255,255,.5)}
.hero-badge{position:absolute;left:180px;top:443px;width:152px;height:152px;border-radius:50%;background:var(--white);display:flex;align-items:center;justify-content:center;color:var(--blue);font-size:22px;font-weight:500;box-shadow:0 4px 12px rgba(0,0,0,.15)}

/* who we are */
.who{top:675px;height:616px}
.who .text{position:absolute;left:145px;top:130px;width:420px}
.who h2{margin-top:8px;margin-bottom:12px}
.who p{margin-bottom:12px}
.who .btn{width:130px;height:41px;margin-top:22px}
.who-photo{position:absolute;left:655px;top:95px;width:432px;height:432px;border-radius:50%;background:radial-gradient(circle at 45% 45%,#f2d4dc 0%,#b9c6ef 30%,#3f63d8 65%,#2c46b7 100%)}

/* expertise */
.expertise{top:1291px;height:606px;background:var(--grey-bg)}
.card{position:absolute;top:172px;width:287px;height:342px;background:var(--white);border-radius:6px;box-shadow:0 6px 18px rgba(0,0,0,.06)}
.card .frame{position:absolute;inset:12px;border:1px solid #e2e4ea;border-radius:6px}
.card.featured .frame{border-color:var(--blue)}
.card .icon{position:absolute;left:94px;top:40px;width:98px;height:98px;border-radius:50%;background:var(--blue-soft);display:flex;align-items:center;justify-content:center}
.card.featured .icon{background:var(--blue)}
.card h3{position:absolute;left:0;top:160px;width:287px;text-align:center;color:var(--ink);font-size:21px;font-weight:700;line-height:27px}
.card p{position:absolute;left:26px;top:227px;width:235px;text-align:center;font-size:13.5px;line-height:26px;color:#333}

/* portfolio */
.portfolio{top:1897px;height:708px}
.slide{position:absolute;background:linear-gradient(135deg,#f3f3f3 0%,#d9d9d9 50%,#eeeeee 100%);border-radius:8px}
.slide .obj{position:absolute;border-radius:50%}
.slider-line{position:absolute;top:601px;height:1px;background:var(--line)}
.arrow-btn{position:absolute;top:587px;width:28px;height:28px;border-radius:50%;display:flex;align-items:center;justify-content:center}

/* about */
.about{top:2605px;height:594px;background:var(--grey-bg)}
.about .text{position:absolute;left:140px;top:112px;width:400px}
.about h2{margin:8px 0 10px}
.about p{margin-bottom:10px}
.about .btn{width:240px;height:39px;margin-top:22px}
.about-photo{position:absolute;left:605px;top:93px;width:453px;height:408px;border-radius:10px 10px 4px 4px;background:linear-gradient(160deg,#8ea1b8 0%,#6c7d96 40%,#4b5a72 100%)}
.about-badge{position:absolute;left:543px;top:382px;width:140px;height:140px;border-radius:50%;background:var(--white);display:flex;align-items:center;justify-content:center;color:var(--blue);font-size:21px;font-weight:500;box-shadow:0 4px 12px rgba(0,0,0,.12)}

/* testimonials */
.reviews{top:3199px;height:599px}
.review-card{position:absolute;left:284px;top:200px;width:634px;height:289px;background:var(--white);box-shadow:0 6px 24px rgba(0,0,0,.10);border-radius:4px}
.quote-badge{position:absolute;left:573px;top:175px;width:54px;height:54px;border-radius:50%;background:var(--blue);display:flex;align-items:center;justify-content:center}
.review-text{position:absolute;left:330px;top:249px;width:540px;text-align:center;font-size:13.5px;line-height:25px;color:#333}
.reviewer{position:absolute;left:0;top:388px;width:1200px;text-align:center;font-size:16px;font-weight:500;color:var(--ink)}
.role{position:absolute;left:0;top:414px;width:1200px;text-align:center;font-size:14px;color:#666}

/* cta */
.cta{top:3798px;height:340px;background:linear-gradient(180deg,#e7e9ec 0%,#dfe1e5 50%,#e6e7ea 100%)}
.cta h2{position:absolute;top:88px}
.cta p{position:absolute;top:130px;left:300px;width:600px;text-align:center;font-size:14.5px;line-height:26px;color:#333}
.cta .btn{position:absolute;left:545px;top:205px;width:112px;height:39px}

/* footer */
.site-footer{top:4138px;height:377px;background:var(--blue);color:var(--white)}
.site-footer h4{position:absolute;top:64px;font-size:16px;font-weight:600;letter-spacing:.4px}
.site-footer h4::after{content:"";display:block;width:30px;height:2px;background:var(--white);margin-top:9px}
.quick a{position:absolute;left:140px;font-size:12px;color:var(--white);text-decoration:none}
.detail{position:absolute;left:356px;font-size:12px;line-height:19px}
.detail b{font-weight:600;display:block}
.detail svg{position:absolute;left:-24px;top:3px}
.follow{position:absolute;left:653px;display:flex;align-items:center;gap:12px;font-size:12px}
.follow span.dot{width:26px;height:26px;border-radius:50%;border:1.5px solid var(--white)}
.footer-brand{position:absolute;left:858px;top:62px;width:200px;display:flex;flex-direction:column;align-items:center;gap:18px}
.footer-brand .mark{width:94px;height:94px;border-radius:50%;border:8px solid var(--white)}
.footer-brand .name{font-size:48px;font-weight:500;letter-spacing:3px}
.copyright{position:absolute;left:0;top:340px;width:1200px;text-align:center;font-size:11px;color:#e6ecff}
.rule{position:absolute;left:140px;top:316px;width:918px;height:1px;background:rgba(255,255,255,.35)}
</style>
</head>
<body>

<div class="abs topbar">
  <span class="social" style="left:55px"></span>
  <span class="social" style="left:91px"></span>
  <span class="social" style="left:127px"></span>
  <div class="contact" style="left:242px">
    <svg width="16" height="16" viewBox="0 0 24 24" fill="none" stroke="#fff" stroke-width="2"><path d="M5 3h4l2 5-2.5 1.5a11 11 0 0 0 6 6L16 13l5 2v4a2 2 0 0 1-2 2A16 16 0 0 1 3 5a2 2 0 0 1 2-2z"/></svg>
    44 (0) 7700900123
  </div>
  <div class="contact" style="left:392px">
    <svg width="18" height="14" viewBox="0 0 24 18" fill="none" stroke="#fff" stroke-width="2"><rect x="1" y="1" width="22" height="16"/><path d="M1 1l11 9 11-9"/></svg>
    info@valtorix.design
  </div>
</div>

<header class="site-header">
  <div class="brand"><span class="mark"></span><span class="name">valtorix</span></div>
  <nav class="nav">
    <a class="active" style="left:501px">HOME</a>
    <a style="left:592px">ABOUT US</a>
    <a style="left:709px">PORTFOLIO</a>
    <a style="left:836px">OUR SERVICES</a>
    <a style="left:978px">CONTACT US</a>
  </nav>
</header>

<section class="hero">
  <div class="hero-photo" role="img" aria-label="Engineers reviewing a 3D CAD model of a mechanical part on a monitor"></div>
  <div class="hero-stripe"></div>
  <div class="hero-circle"></div>
  <h1 class="hero-title">Precision<br>Engineering<br>&amp; Mechanical<br>Design</h1>
  <p class="hero-sub">Transforming concepts into production-ready designs with expertise and innovation</p>
  <a class="hero-btn">Contact us Today</a>
  <div class="hero-badge">valtorix</div>
</section>

<section class="who">
  <div class="text">
    <div class="eyebrow">WHO WE ARE</div>
    <h2 class="section-title">VALTORIX DESIGN</h2>
    <p class="body-copy">Welcome to Valtorix Design. We are a UK based design consultancy offering a comprehensive mechanical and product design service from initial concepts through to full volume production.</p>
    <p class="body-copy">Duis autem vel eum iriure dolor in hendrerit in vulputate velit esse molestie consequat, vel illum dolore eu feugiat nulla facilisis at vero eros et accumsan et iusto odio dignissim qui blandit praesent luptatum zzril delenit augue duis dolore te feugait nulla facilisi tincidunt ut laoreet.</p>
    <a class="btn">READ MORE</a>
  </div>
  <div class="who-photo" role="img" aria-label="Designer working on CAD drawings at a desk, framed in a circle"></div>
</section>

<section class="expertise">
  <div class="abs eyebrow center" style="top:86px">Solutions</div>
  <h2 class="abs section-title center" style="top:114px">OUR EXPERTISE</h2>

  <div class="card" style="left:142px">
    <div class="frame"></div>
    <div class="icon">
      <svg width="50" height="36" viewBox="0 0 50 36" fill="none" stroke="#5673e0" stroke-width="2" stroke-linejoin="round"><path d="M2 8l9-4 8 4M48 8l-9-4-10 5-8 6a3 3 0 0 0 4 4l7-5"/><path d="M11 4v16l10 10a3 3 0 0 0 4-2l3 2a3 3 0 0 0 4-3 3 3 0 0 0 4-3 3 3 0 0 0 3-4L39 8"/><path d="M2 8l6 14M48 8l-6 14"/></svg>
    </div>
    <h3>Bespoke<br>Product Design</h3>
    <p>Innovative design from concept through the full development life cycle</p>
  </div>

  <div class="card featured" style="left:455px">
    <div class="frame"></div>
    <div class="icon">
      <svg width="46" height="44" viewBox="0 0 46 44" fill="none" stroke="#fff" stroke-width="2" stroke-linejoin="round"><rect x="2" y="2" width="42" height="30" rx="2"/><path d="M16 42h14M23 32v10"/><path d="M23 9l9 5v9l-9 5-9-5v-9z M14 14l9 5 9-5M23 19v9"/></svg>
    </div>
    <h3>3D Modelling and<br>Drawings</h3>
    <p>We create 3D CAD, 2D engineering drawings and photorealistic renders</p>
  </div>

  <div class="card" style="left:771px">
    <div class="frame"></div>
    <div class="icon">
      <svg width="44" height="40" viewBox="0 0 44 40" fill="none" stroke="#5673e0" stroke-width="2" stroke-linejoin="round"><path d="M3 38V4h6v18l10-7v7l10-7v7l10-7v23z"/><rect x="12" y="28" width="4" height="4" fill="#5673e0"/><rect x="20" y="28" width="4" height="4" fill="#5673e0"/><rect x="28" y="28" width="4" height="4" fill="#5673e0"/></svg>
    </div>
    <h3>Design for<br>Manufacture</h3>
    <p>Creating designs optimised for prototype and production manufacture</p>
  </div>
</section>

<section class="portfolio">
  <div class="abs eyebrow center" style="top:86px">Projects</div>
  <h2 class="abs section-title center" style="top:116px">OUR PORTFOLIO</h2>
  <p class="abs center" style="top:163px;font-size:14px;color:#333">A small selection of our previous projects</p>

  <div class="slide" style="left:-8px;top:225px;width:369px;height:299px" role="img" aria-label="Render of a chrome alloy wheel"></div>
  <div class="slide" style="left:385px;top:203px;width:430px;height:340px" role="img" aria-label="Render of an action camera mounted on a yellow threaded slide rail"></div>
  <div class="slide" style="left:839px;top:225px;width:369px;height:299px" role="img" aria-label="Render of a go-kart chassis with steering wheel and seat"></div>

  <div class="slider-line" style="left:298px;width:263px"></div>
  <div class="slider-line" style="left:645px;width:263px"></div>
  <div class="arrow-btn" style="left:568px;background:#8a8a8a">
    <svg width="10" height="10" viewBox="0 0 10 10" fill="none" stroke="#fff" stroke-width="2"><path d="M6.5 1.5L3 5l3.5 3.5"/></svg>
  </div>
  <div class="arrow-btn" style="left:604px;background:var(--blue)">
    <svg width="10" height="10" viewBox="0 0 10 10" fill="none" stroke="#fff" stroke-width="2"><path d="M3.5 1.5L7 5 3.5 8.5"/></svg>
  </div>
</section>

<section class="about">
  <div class="text">
    <div class="eyebrow">About Me</div>
    <h2 class="section-title">OWEN PRYCE</h2>
    <p class="body-copy">Owen Pryce is the Chief Engineer at Valtorix Design. He has 11 years experience working as a mechanical design engineer in multiple industries including high performance automotive, consumer products, medical, industrial plus many more. He has worked in multiple roles across a wide range of products.</p>
    <p class="body-copy">Ut wisi enim ad minim veniam, quis nostrud exerci t ullamcorper suscipit lobortis nisl ut aliquip ex ea commodo consequat. Duis autem vel eum iriure dolor in hendrerit.</p>
    <a class="btn">TELL US ABOUT YOUR IDEAS</a>
  </div>
  <div class="about-photo" role="img" aria-label="Portrait photograph of the chief engineer"></div>
  <div class="about-badge">valtorix</div>
</section>

<section class="reviews">
  <div class="abs eyebrow center" style="top:90px">Testimonials</div>
  <h2 class="abs section-title center" style="top:118px">CUSTOMER REVIEWS</h2>
  <div class="review-card"></div>
  <div class="quote-badge">
    <svg width="26" height="20" viewBox="0 0 26 20" fill="#fff"><path d="M0 12a8 8 0 0 1 8-12v4a4 4 0 0 0-3 4h3v12H0zM14 12a8 8 0 0 1 8-12v4a4 4 0 0 0-3 4h3v12h-8z"/></svg>
  </div>
  <p class="review-text">"Owen is able to bridge the gap between what management want and what manufacturing can deliver.<br>In the field of Casting his intuition for the process and knowledge of casting technical nuances means he is able to push both the design and guide manufacturers to produce excellent results."</p>
  <div class="reviewer">Martin Hale</div>
  <div class="role">Design Engineer</div>
  <svg class="abs" style="left:579px;top:444px" width="42" height="12" viewBox="0 0 42 12" fill="none" stroke="#2f5de6" stroke-width="1.5"><path d="M16 6H2M6 2L2 6l4 4M26 6h14M36 2l4 4-4 4"/></svg>
</section>

<section class="cta" role="img" aria-label="Faint background of technical engineering sketches">
  <h2 class="section-title center">CURIOUS WHAT ELSE WE DO?</h2>
  <p>Duis autem vel eum iriure dolor in hendrerit in vulputate velit esse molestie consequat, vel illum dolore eu feugiat nulla facilisis at vero eros et accumsan.</p>
  <a class="btn">SEE HERE</a>
</section>

<footer class="site-footer">
  <h4 style="left:140px">QUICK LINKS</h4>
  <h4 style="left:356px">CONTACT DETAILS</h4>
  <h4 style="left:653px">FOLLOW US</h4>

  <div class="quick">
    <a style="top:115px">· Home</a>
    <a style="top:144px">· About Us</a>
    <a style="top:173px">· Our Services</a>
    <a style="top:202px">· Portfolio</a>
    <a style="top:231px">· Contact Us</a>
  </div>

  <div class="detail" style="top:112px">
    <svg width="12" height="16" viewBox="0 0 12 16" fill="#fff"><path d="M6 0a6 6 0 0 1 6 6c0 4-6 10-6 10S0 10 0 6a6 6 0 0 1 6-6zm0 3.5a2.5 2.5 0 1 0 0 5 2.5 2.5 0 0 0 0-5z"/></svg>
    <b>ADDRESS</b>Foundry Yard Road, Cardiff, UK
  </div>
  <div class="detail" style="top:166px">
    <svg width="14" height="14" viewBox="0 0 24 24" fill="#fff"><path d="M5 2h4l2 5-2.5 1.5a11 11 0 0 0 6 6L16 12l5 2v4a2 2 0 0 1-2 2A17 17 0 0 1 3 4a2 2 0 0 1 2-2z"/></svg>
    <b>PHONE</b>+44 (0)7700 900 123
  </div>
  <div class="detail" style="top:221px">
    <svg width="15" height="11" viewBox="0 0 24 18" fill="#fff"><path d="M0 0h24v2L12 10 0 2z M0 5l12 8 12-8v13H0z"/></svg>
    <b>EMAIL</b>info@valtorix.design
  </div>

  <div class="follow" style="top:117px"><span class="dot"></span>Socialboard</div>
  <div class="follow" style="top:154px"><span class="dot"></span>Vidstream</div>
  <div class="follow" style="top:192px"><span class="dot"></span>Snapgrid</div>
  <div class="follow" style="top:229px"><span class="dot"></span>Proflink</div>

  <div class="footer-brand"><span class="mark"></span><span class="name">valtorix</span></div>

  <div class="rule"></div>
  <div class="copyright">© 2025 Valtorix Design. All Rights Reserved.</div>
</footer>

</body>
</html>
```